Card design for orthopaedic surgeons working as The Brightwater Joint Centre

Business cards, letterhead

Colors

Designer to choose colors to be used in the design.

Requirements
Must have
• Late addition.
• Cards letterhead must have logos of
• Crestmoor Lindell College of Surgeons
• Varenwood Bone Health Association
Nice to have
• Back of card to have space for appointment time to be added by hand and some blank space for writing incidental other notes.

```html
<!DOCTYPE html>
<html lang="en">
<head>
<meta charset="utf-8">
<title>The Brightwater Joint Centre — Business Cards</title>
<link rel="stylesheet" href="https://fonts.googleapis.com/css2?family=Source+Sans+3:wght@400;600;700&display=swap">
<style>
  :root {
    --backdrop: #e6e8eb;
    --navy: #073a57;
    --navy-deep: #042c45;
    --teal: #0a5670;
    --sky: #3aa6f2;
    --sky-light: #55b8f7;
    --ink: #1f2f3d;
    --white: #ffffff;
    --dots: #4a5560;
  }
  * { margin: 0; padding: 0; box-sizing: border-box; }
  html, body {
    width: 1200px; height: 960px; overflow: hidden;
    background: var(--backdrop);
    font-family: "Source Sans 3", Arial, sans-serif;
  }
  .canvas { position: relative; width: 1200px; height: 960px; }

  .card {
    position: absolute;
    width: 700px; height: 400px;
    border-radius: 26px;
    overflow: hidden;
    background: var(--white);
    box-shadow: 0 10px 28px rgba(0,0,0,0.18);
  }

  /* Appointment card (back) */
  .appointment { left: 110px; top: 60px; }
  .appointment .header-band {
    position: absolute; left: 0; top: 0; width: 100%; height: 132px;
    background: linear-gradient(100deg, var(--navy-deep), var(--teal));
  }
  .appointment .wordmark {
    position: absolute; right: 40px; top: 46px;
    color: var(--sky-light); font-size: 36px; font-weight: 400;
    letter-spacing: -0.5px; white-space: nowrap;
  }
  .appointment .fields {
    position: absolute; left: 44px; top: 168px; right: 44px;
  }
  .field-row {
    display: flex; align-items: baseline; gap: 10px;
    margin-bottom: 34px;
    color: var(--sky); font-size: 22px; font-weight: 600;
  }
  .field-line {
    flex: 1; border-bottom: 2px dotted var(--dots); height: 18px;
  }
  .field-suffix { font-size: 14px; font-weight: 400; }
  .appointment .notice-band {
    position: absolute; left: 0; bottom: 0; width: 100%; height: 52px;
    background: linear-gradient(90deg, var(--sky), var(--sky-light));
    color: var(--white); font-size: 18px;
    display: flex; align-items: center; justify-content: center;
    white-space: nowrap;
  }

  /* Contact card (front) */
  .contact { left: 400px; top: 500px; }
  .contact .wave { position: absolute; inset: 0; }
  .contact .details {
    position: absolute; left: 44px; top: 48px; color: var(--ink);
  }
  .person-name {
    color: var(--sky); font-size: 28px; font-weight: 700; letter-spacing: 0.5px;
  }
  .person-role {
    color: var(--navy); font-size: 18px; font-weight: 600; margin-bottom: 14px;
  }
  .address { font-size: 18px; line-height: 1.25; margin-bottom: 12px; padding-left: 26px; }
  .contact-list { list-style: none; }
  .contact-list li {
    display: flex; align-items: center; gap: 10px;
    font-size: 18px; line-height: 1.35; white-space: nowrap;
  }
  .contact-list svg { width: 16px; height: 16px; flex: none; fill: var(--sky); }
  .contact .wordmark {
    position: absolute; right: 26px; top: 228px;
    color: var(--sky-light); font-size: 28px; font-weight: 400;
    line-height: 1.15; text-align: right; letter-spacing: -0.3px;
  }
</style>
</head>
<body>
<main class="canvas">

  <section class="card appointment" aria-label="Appointment card">
    <div class="header-band"></div>
    <div class="wordmark">The Brightwater Joint Centre</div>
    <div class="fields">
      <div class="field-row"><span>Name :</span><span class="field-line"></span></div>
      <div class="field-row">
        <span>Date :</span><span class="field-line"></span>
        <span>Time :</span><span class="field-line"></span>
        <span class="field-suffix">AM/PM</span>
      </div>
    </div>
    <div class="notice-band">Please give 24 hours notice cancelling your appointment or a fee may be charged</div>
  </section>

  <section class="card contact" aria-label="Business card">
    <svg class="wave" viewBox="0 0 700 400" preserveAspectRatio="none" aria-hidden="true">
      <defs>
        <linearGradient id="panelFill" x1="0" y1="0" x2="1" y2="1">
          <stop offset="0" stop-color="#0a5670"/>
          <stop offset="1" stop-color="#063550"/>
        </linearGradient>
      </defs>
      <path d="M700 50 C560 50 500 120 440 250 C390 360 320 385 230 400 L700 400 Z" fill="url(#panelFill)"/>
      <path d="M640 52 C545 56 488 128 430 255 C385 355 318 380 240 394" fill="none" stroke="#3aa6f2" stroke-width="6"/>
      <path d="M625 56 C535 64 478 135 422 258 C378 352 315 375 245 388" fill="none" stroke="#042c45" stroke-width="3"/>
    </svg>
    <div class="details">
      <div class="person-name">DANIEL HARROW</div>
      <div class="person-role">President</div>
      <div class="address">42 Larkfield Road<br>Millbrook, Oregon 58210</div>
      <ul class="contact-list">
        <li><svg viewBox="0 0 16 16"><path d="M3 1l3 3-1.5 2a9 9 0 0 0 5.5 5.5L12 10l3 3-2 2C7 15 1 9 1 3z"/></svg>555-204-7731</li>
        <li><svg viewBox="0 0 16 16"><path d="M4 0h8a1 1 0 0 1 1 1v14a1 1 0 0 1-1 1H4a1 1 0 0 1-1-1V1a1 1 0 0 1 1-1zm1 2v10h6V2z"/></svg>555-318-6642</li>
        <li><svg viewBox="0 0 16 16"><path d="M4 1h8v4H4zM1 6h14v7h-3v2H4v-2H1zm4 5v3h6v-3z"/></svg>555-427-1190</li>
        <li><svg viewBox="0 0 16 16"><path d="M1 3h14v10H1zm1 1.5V5l6 4 6-4v-.5z"/></svg>daniel@brightwaterjoint.com</li>
        <li><svg viewBox="0 0 16 16"><circle cx="8" cy="8" r="7"/></svg>www.brightwaterjoint.com</li>
      </ul>
    </div>
    <div class="wordmark">The Brightwater<br>Joint Centre</div>
  </section>

</main>
</body>
</html>
```